RUVO WARE LTD

Advertisement to get more schools:
use website https://www.ruvo-ware.co.uk for logos etc.
ICT Service Level Agreements for as little as £2000 per year
Unlimited Remote, phone and email support
Unlimited Call outs included
90% fix time within 30 minutes of ticket submission
Extra support during Scolvar inspections
GDPR service included

Education

```html
<!DOCTYPE html>
<html lang="en">
<head>
<meta charset="utf-8">
<title>RUVO WARE LTD – Education, Support and Installation</title>
<link rel="stylesheet" href="https://fonts.googleapis.com/css2?family=Poppins:wght@400;500;600;700&family=Roboto:wght@500;700&display=swap">
<style>
:root{
  --orange:#f7843a;
  --orange-deep:#d95c12;
  --cream:#fff3e3;
  --blue:#1f74c4;
  --blue-bright:#3a8ef5;
  --blue-deep:#1a5fd3;
  --ink:#1f1f1f;
  --white:#ffffff;
}
*{box-sizing:border-box;margin:0;padding:0}
html,body{width:1200px;height:4542px;overflow:hidden;background:var(--white)}
.page{position:relative;width:1200px;height:4542px;overflow:hidden;font-family:"Roboto",sans-serif}
.hero-photo{position:absolute;left:0;top:0;width:1200px;height:940px;
  background:linear-gradient(120deg,#c9a98a 0%,#e8d9c6 22%,#7fb9c4 45%,#d6dde2 65%,#a9b2b8 85%,#6e757a 100%)}
.backdrop{position:absolute;left:0;top:0;width:1200px;height:4542px}
.brand{position:absolute;text-align:center}
.brand-name{font-family:"Poppins",sans-serif;font-weight:700;color:var(--blue);letter-spacing:2px;line-height:1}
.brand-tag{font-family:"Poppins",sans-serif;font-weight:500;color:var(--orange);letter-spacing:1.5px}
.brand--top{left:802px;top:40px;width:362px}
.brand--top .brand-name{font-size:58px}
.brand--top .brand-tag{font-size:16px;margin-top:8px}
.headline{position:absolute;left:578px;top:273px;width:622px;height:273px;background:var(--blue);
  display:flex;align-items:center;justify-content:flex-end;padding-right:26px}
.headline h1{font-family:"Poppins",sans-serif;font-weight:700;color:var(--white);font-size:46px;line-height:61px;text-align:right;letter-spacing:.5px}
.feature{position:absolute;width:420px;text-align:center}
.feature-icon{width:273px;height:273px;margin:0 auto;background:var(--white);border-radius:40px;display:flex;align-items:center;justify-content:center}
.feature-icon svg{width:170px;height:170px}
.feature p{color:var(--cream);font-weight:700;font-size:36px;line-height:62px;margin-top:14px}
.partners-title{position:absolute;left:0;top:3010px;width:1200px;text-align:center;font-family:"Poppins",sans-serif;font-weight:600;font-size:70px;color:var(--ink)}
.partner{position:absolute;display:flex;align-items:center;justify-content:center;gap:22px;font-family:"Poppins",sans-serif;font-weight:600;color:var(--ink)}
.partner-mark{display:block}
.footer-brand{left:400px;top:4222px;width:400px}
.footer-brand .brand-name{font-size:52px;color:var(--white)}
.footer-brand .brand-tag{font-size:15px;color:var(--white);margin-top:10px}
.copyright{position:absolute;left:0;top:4354px;width:1200px;text-align:center;font-family:"Poppins",sans-serif;font-weight:500;font-size:20px;color:var(--white)}
.social{position:absolute;top:4419px;left:0;width:1200px;display:flex;justify-content:center;gap:12px}
.social span{width:62px;height:62px;display:flex;align-items:center;justify-content:center;font-family:"Poppins",sans-serif;font-weight:600;font-size:10px;color:var(--white);background:var(--blue-deep)}
</style>
</head>
<body>
<main class="page">
  <div class="hero-photo" role="img" aria-label="Photograph of a schoolgirl typing on a laptop with floating learning screens"></div>

  <svg class="backdrop" viewBox="0 0 1200 4542" aria-hidden="true">
    <path d="M0,380 C350,540 800,620 1200,890 L1200,3210 C900,2880 500,2700 0,2690 Z" fill="var(--orange-deep)"/>
    <path d="M0,420 C350,575 800,650 1200,925 L1200,3160 C900,2830 500,2660 0,2650 Z" fill="var(--orange)"/>
    <path d="M0,3700 C300,3950 700,4130 1200,4215 L1200,4542 L0,4542 Z" fill="var(--blue-deep)"/>
    <path d="M0,3760 C320,3990 720,4170 1200,4240 L1200,4542 L0,4542 Z" fill="var(--blue-bright)"/>
  </svg>

  <div class="brand brand--top">
    <div class="brand-name">RUVO WARE</div>
    <div class="brand-tag">EDUCATION SUPPORT &amp; INSTALLATION</div>
  </div>

  <div class="headline"><h1>EDUCATION, SUPPORT<br>AND INSTALLATION<br>OF ALL TECHNOLOGIES</h1></div>

  <section class="feature" style="left:135px;top:962px">
    <div class="feature-icon"><svg viewBox="0 0 100 100"><path d="M20 8h45l15 15v69H20z" fill="var(--orange)"/><path d="M65 8v15h15" fill="#ffb27a"/><g stroke="#fff" stroke-width="4" stroke-linecap="round"><line x1="30" y1="28" x2="50" y2="28"/><line x1="30" y1="40" x2="65" y2="40"/><line x1="30" y1="52" x2="70" y2="52"/><line x1="30" y1="64" x2="55" y2="64"/></g><path d="M52 82c4-10 8-8 6 0s6-2 12 0" stroke="#fff" stroke-width="3.5" fill="none" stroke-linecap="round"/></svg></div>
    <p>ICT SLA agreements<br>for as little as £2000<br>per year</p>
  </section>
  <section class="feature" style="left:645px;top:962px">
    <div class="feature-icon"><svg viewBox="0 0 100 100"><path d="M38 14a18 18 0 0 1 24 0M43 20a10 10 0 0 1 14 0" stroke="var(--orange)" stroke-width="5" fill="none" stroke-linecap="round"/><rect x="30" y="28" width="40" height="64" rx="9" fill="var(--orange)"/><g fill="#fff"><circle cx="41" cy="42" r="3"/><circle cx="50" cy="42" r="3"/><circle cx="59" cy="42" r="3"/><circle cx="41" cy="53" r="3"/><circle cx="50" cy="53" r="3"/><circle cx="59" cy="53" r="3"/></g><circle cx="50" cy="74" r="9" fill="none" stroke="#fff" stroke-width="5"/></svg></div>
    <p>Unlimited Remote,<br>phone and email<br>support</p>
  </section>
  <section class="feature" style="left:135px;top:1533px">
    <div class="feature-icon"><svg viewBox="0 0 100 100"><path d="M22 10l14 4 6 18-9 8c5 11 13 19 24 24l8-9 18 6 4 14c-4 8-12 12-22 10C40 80 20 60 14 34c-2-10 2-18 8-24z" fill="var(--orange)"/><path d="M56 20a22 22 0 0 1 22 22M56 8a34 34 0 0 1 34 34" stroke="var(--orange)" stroke-width="6" fill="none" stroke-linecap="round"/></svg></div>
    <p>Unlimited Call outs<br>included</p>
  </section>
  <section class="feature" style="left:645px;top:1533px">
    <div class="feature-icon"><svg viewBox="0 0 100 100"><rect x="20" y="16" width="60" height="76" rx="3" fill="var(--orange)"/><rect x="36" y="8" width="28" height="14" rx="4" fill="var(--orange)" stroke="#fff" stroke-width="3"/><circle cx="50" cy="57" r="18" fill="none" stroke="#fff" stroke-width="5"/><path d="M41 57l7 7 12-13" stroke="#fff" stroke-width="5" fill="none" stroke-linecap="round" stroke-linejoin="round"/></svg></div>
    <p>90% fix time within 30<br>minutes of ticket<br>submission</p>
  </section>
  <section class="feature" style="left:135px;top:2120px">
    <div class="feature-icon"><svg viewBox="0 0 100 100"><rect x="20" y="10" width="60" height="80" rx="6" fill="var(--orange)"/><g stroke="#fff" stroke-width="5" stroke-linecap="round" stroke-linejoin="round" fill="none"><path d="M29 30l5 5 8-9M29 50l5 5 8-9M29 70l5 5 8-9"/><line x1="50" y1="31" x2="70" y2="31"/><line x1="50" y1="51" x2="70" y2="51"/><line x1="50" y1="71" x2="70" y2="71"/></g></svg></div>
    <p>Extra support during<br>Scolvar inspections</p>
  </section>
  <section class="feature" style="left:645px;top:2120px">
    <div class="feature-icon"><svg viewBox="0 0 100 100"><path d="M50 6l36 12v26c0 24-16 40-36 50C30 84 14 68 14 44V18z" fill="var(--orange)"/><text x="50" y="34" text-anchor="middle" font-family="Poppins, sans-serif" font-weight="700" font-size="13" fill="#fff">GDPR</text><rect x="37" y="52" width="26" height="22" rx="3" fill="#fff"/><path d="M42 52v-6a8 8 0 0 1 16 0v6" stroke="#fff" stroke-width="4" fill="none"/><circle cx="50" cy="62" r="3" fill="var(--orange)"/></svg></div>
    <p>GDPR service<br>included</p>
  </section>

  <h2 class="partners-title">Partners</h2>

  <div class="partner" style="left:123px;top:3180px;width:435px;height:160px" role="img" aria-label="Authorised partner badge">
    <svg class="partner-mark" width="430" height="160" viewBox="0 0 430 160"><rect x="3" y="3" width="424" height="154" rx="40" fill="#0d5f5a"/></svg>
  </div>
  <div class="partner" style="left:640px;top:3180px;width:418px;height:160px;font-size:60px">
    <svg class="partner-mark" width="40" height="40"><rect width="40" height="40" fill="#e1262c"/></svg>Tavrona
  </div>
  <div class="partner" style="left:140px;top:3453px;width:400px;height:142px;font-size:60px">
    <svg class="partner-mark" width="40" height="40"><rect width="40" height="40" fill="#83b81a"/></svg>Quillon
  </div>
  <div class="partner" style="left:632px;top:3453px;width:460px;height:142px;font-size:60px">
    <svg class="partner-mark" width="40" height="40"><rect width="40" height="40" fill="#737373"/></svg>Meridex
  </div>
  <div class="partner" style="left:320px;top:3710px;width:560px;height:140px;font-size:72px">
    <svg class="partner-mark" width="44" height="44"><circle cx="22" cy="22" r="22" fill="#2d5aa8"/></svg>Safelane
  </div>

  <div class="brand footer-brand">
    <div class="brand-name">RUVO WARE</div>
    <div class="brand-tag">EDUCATION SUPPORT &amp; INSTALLATION</div>
  </div>
  <p class="copyright">© Copyrights 2022 Company name | All Rights Reserved</p>
  <nav class="social" aria-label="Social links">
    <span>Linkbook</span><span>Chirp</span><span>Vidstream</span>
  </nav>
</main>
</body>
</html>
```